Small corporate website template design

I need a couple templates designed for a small corporate website. The corporate site reflects the existence of the parent company which will own various brands/services that have their own websites, so it will mainly be used to present who we are, what we do, what is happening (news/events), how to contact us, link off to our other brand/service sites, as well as post information for public relations, investors, and job opportunities.

The company name is Brelvanto LLC (www.brelvanto-example.com), and the name is representative of stratified layers of interconnected digital services. The corporate site is not expected to generate a bunch of fanfare - that honor will be reserved for the externally linked brand/service sites.

The provided logo may be manipulated in color, size, shape, positioning, etc. to get it to fit with the design, but should be integrated in some way.

What we are looking for is a home page layout as well as a template for an inner page whereby the navigation/logo, etc may be diminished to some extent for the inner pages. We are also interested in reusable elements such as dividers, content containers, etc. in order to represent the types of information described above that we would like to present as described above.

We are particularly interested in consistency of design elements, conservative use of color (including consideration of accessibility concerns), judicious use of whitespace in favor of simplified messaging, and something lending itself well to internationalization/translation.

Target Market(s)

Small business owners, entrepreneurs (B2B)

Number of Pages Required

2 page

Font styles to use
Sans Serif

Requirements
Must have
• See the attached PDF with the logo concept, color swatches, and comparative sites.

```html
<!DOCTYPE html>
<html lang="en">
<head>
<meta charset="utf-8">
<title>Brelvanto LLC</title>
<link rel="stylesheet" href="https://fonts.googleapis.com/css2?family=Open+Sans:wght@400;600;700&family=Raleway:wght@600;700;800&display=swap">
<style>
:root{
  --navy:#0c2a5c;
  --teal:#0f4a5e;
  --green:#1b7a3c;
  --pale:#eef5f9;
  --band:#f0f5f9;
  --ink:#1d1d1d;
  --text:#555b61;
  --orange:#f0901e;
  --accent:#e2531d;
  --line:#d5d9dd;
  --white:#ffffff;
}
*{margin:0;padding:0;box-sizing:border-box}
html,body{width:1200px;height:2848px;overflow:hidden;background:var(--white)}
body{position:relative;font-family:"Open Sans",Arial,sans-serif;color:var(--text)}
.abs{position:absolute}
.heading{font-family:"Raleway",Arial,sans-serif;color:var(--ink);font-weight:700}
.hero-bg{position:absolute;left:0;top:0}
.brand{left:80px;top:20px;text-align:center;color:var(--white);font-family:"Raleway",sans-serif;font-weight:700;font-size:20px}
.brand .mark{width:70px;height:70px;border-radius:50%;background:var(--white);margin:0 auto 14px}
.menu-btn{left:955px;top:16px;width:40px;height:40px;border-radius:50%;background:var(--orange)}
.menu-btn span{position:absolute;left:12px;width:16px;height:3px;background:var(--white);border-radius:2px}
.signin{left:1008px;top:22px;width:92px;height:32px;border:2px solid var(--orange);border-radius:16px;color:var(--orange);font-size:13px;font-weight:700;text-align:center;line-height:28px}
.signin i{display:inline-block;width:8px;height:8px;background:var(--orange);border-radius:1px;margin-right:5px}
.hero-title{left:97px;top:200px;font-family:"Raleway",sans-serif;font-weight:800;font-size:46px;line-height:65px;color:var(--white);letter-spacing:.5px}
.btn-outline{border:2px solid var(--white);border-radius:28px;color:var(--white);font-weight:700;font-size:15px;text-align:center}
.hero-btn{left:97px;top:425px;width:172px;height:54px;line-height:50px}
.hero-art{left:690px;top:90px;width:480px;height:350px;border-radius:30px;background:linear-gradient(160deg,#ffffff 0%,#e3e9ee 60%,#cfd8df 100%)}
.section-title{left:0;width:1200px;text-align:center;font-size:40px}
.lead{left:210px;width:780px;text-align:center;font-size:15px;line-height:29px}
.card{width:470px;height:296px;border:1px solid var(--line);background:var(--white);text-align:center}
.card h3{margin-top:90px;font-family:"Raleway",sans-serif;font-weight:600;font-size:25px;color:var(--ink)}
.card p{margin:18px auto 0;width:420px;font-size:14.5px;line-height:29px}
.card .more{display:block;margin-top:16px;color:var(--orange);font-weight:700;font-size:15px}
.hex{width:134px;height:116px}
.band{left:0;top:1315px;width:1200px;height:452px;background:var(--band)}
.news-img{width:216px;height:184px;border:3px solid var(--white);box-shadow:0 1px 4px rgba(0,0,0,.25)}
.news h4{font-family:"Raleway",sans-serif;font-size:20px;font-weight:700;color:var(--ink)}
.news .meta{margin-top:10px;font-size:12px;color:#444}
.news .meta b{display:inline-block;width:9px;height:9px;background:var(--accent);margin-right:6px;border-radius:2px}
.news p{margin-top:12px;width:240px;font-size:12px;line-height:25px}
.news .more{display:block;margin-top:12px;color:var(--accent);font-weight:700;font-size:14px}
.brand-box{top:1934px;width:188px;height:106px;border:1px solid #c9cdd1;text-align:center;line-height:104px;font-family:"Raleway",sans-serif;font-weight:700;font-size:30px;color:#8a8f94}
.contact-bg{left:0;top:2133px}
.contact-title{color:var(--white);font-size:38px}
.contact-lead{color:var(--white);font-size:15px;line-height:29px;left:210px;width:780px;text-align:center}
.contact-btn{left:516px;top:2332px;width:170px;height:54px;line-height:50px}
.foot-brand{left:150px;top:2555px;width:170px;text-align:center;font-family:"Raleway",sans-serif;font-weight:700;font-size:24px;color:#111}
.foot-brand .mark{width:100px;height:100px;border-radius:50%;background:#111;margin:0 auto 36px}
.foot-col h5{font-family:"Raleway",sans-serif;font-size:18px;font-weight:700;color:var(--ink);margin-bottom:14px}
.foot-col li{list-style:none;font-size:12px;line-height:23px;color:#444}
.foot-col p{font-size:12px;line-height:22px;color:#444}
.email-field{margin-top:16px;width:252px;border-bottom:1px solid #bbb;font-size:11px;color:#888;padding-bottom:8px}
.subscribe{margin-top:17px;width:98px;height:29px;border:2px solid var(--orange);border-radius:15px;color:var(--orange);font-size:11px;font-weight:700;text-align:center;line-height:25px}
.contact-row{position:relative;padding-left:29px;font-size:12px;line-height:19px;color:#333;margin-bottom:20px}
.contact-row svg{position:absolute;left:0;top:2px}
.rule{left:99px;top:2768px;width:1001px;height:1px;background:#ccc}
.copy{left:99px;top:2799px;font-size:11.5px;color:#333}
.social{top:2796px;width:25px;height:25px;border:1.5px solid var(--orange);border-radius:50%}
.social::after{content:"";position:absolute;left:8px;top:8px;width:6px;height:6px;border-radius:50%;background:var(--orange)}
</style>
</head>
<body>

<svg class="hero-bg" width="1200" height="690" viewBox="0 0 1200 690" aria-hidden="true">
  <defs>
    <linearGradient id="heroGrad" x1="0" y1="0.8" x2="1" y2="0">
      <stop offset="0" stop-color="#0a2456"/>
      <stop offset="0.55" stop-color="#0d3a5e"/>
      <stop offset="1" stop-color="#1b7a3c"/>
    </linearGradient>
  </defs>
  <polygon points="0,0 706,0 580,289 706,513 0,675" fill="url(#heroGrad)"/>
  <polygon points="580,289 706,0 1110,0 1200,110 1200,470 1101,589 706,513" fill="#eef5f9"/>
  <polygon points="1110,0 1200,0 1200,110" fill="#1b7a3c"/>
</svg>

<header>
  <div class="abs brand"><div class="mark"></div>Brelvanto</div>
  <div class="abs menu-btn" aria-label="Menu"><span style="top:13px"></span><span style="top:19px"></span><span style="top:25px"></span></div>
  <div class="abs signin"><i></i>SIGN IN</div>
</header>

<section class="hero">
  <h1 class="abs hero-title">DIGITAL LAYERS TO<br>RAISE THE QUALITY<br>OF LIFE</h1>
  <div class="abs btn-outline hero-btn">GET MORE INFO</div>
  <div class="abs hero-art" role="img" aria-label="Illustration of a smartphone showing a colourful pie chart and data dashboard"></div>
</section>

<section class="welcome">
  <h2 class="abs heading section-title" style="top:656px">Welcome to Brelvanto</h2>
  <p class="abs lead" style="top:727px">Nam libero tempore, cum soluta nobis est eligendi optio cumque nihil impedit quo minus id quod maxime place at facere possimus, omnis voluptas assumenda est, omnis dolor repellesdam et aut officiis debitis aut rerum nece ssitatibus saepe eveniet ut et voluptates repudiandae sint et mole andae.</p>

  <div class="abs card" style="left:99px;top:923px">
    <h3>Who We Are</h3>
    <p>Nam libero tempore, cum soluta nobis est eligendi optio cumque nihil impedit quo minus id quod maxime placeat fac ere possimus, omnis voluptas assumend</p>
    <span class="more">READ MORE</span>
  </div>
  <svg class="abs hex" style="left:267px;top:864px" viewBox="0 0 134 116" aria-hidden="true">
    <polygon points="33,0 101,0 134,58 101,116 33,116 0,58" fill="#e3f0f1"/>
    <circle cx="67" cy="46" r="10" fill="#1b7a3c"/>
    <path d="M48 78 Q48 60 67 60 Q86 60 86 78 Z" fill="#0c2a5c"/>
  </svg>

  <div class="abs card" style="left:630px;top:923px">
    <h3>What We Do</h3>
    <p>Nam libero tempore, cum soluta nobis est eligendi optio cumque nihil impedit quo minus id quod maxime placeat fac ere possimus, omnis voluptas assumend</p>
    <span class="more">READ MORE</span>
  </div>
  <svg class="abs hex" style="left:798px;top:864px" viewBox="0 0 134 116" aria-hidden="true">
    <polygon points="33,0 101,0 134,58 101,116 33,116 0,58" fill="#e3f0f1"/>
    <circle cx="60" cy="62" r="14" fill="none" stroke="#0c2a5c" stroke-width="8" stroke-dasharray="5 3"/>
    <circle cx="60" cy="62" r="5" fill="#0c2a5c"/>
    <circle cx="82" cy="46" r="8" fill="none" stroke="#1b7a3c" stroke-width="5" stroke-dasharray="4 2"/>
    <circle cx="82" cy="76" r="8" fill="none" stroke="#1b7a3c" stroke-width="5" stroke-dasharray="4 2"/>
  </svg>
</section>

<section class="happening">
  <div class="abs band"></div>
  <h2 class="abs heading section-title" style="top:1388px">What is Happening</h2>

  <div class="abs news-img" style="left:99px;top:1486px;background:linear-gradient(135deg,#2b4c73,#8aa2bd 60%,#d6dde4)" role="img" aria-label="Photo of colleagues reviewing printed charts on a desk"></div>
  <div class="abs news" style="left:344px;top:1480px">
    <h4>At vero eos et accu samu</h4>
    <div class="meta"><b></b>17/08/2017 &nbsp;|&nbsp; <b></b>Mara Lind</div>
    <p>Temporibus autem quibusdam et aut offi cis debitis aut rerum necessitatibus sae pe eveniet ut et voluptates.</p>
    <span class="more">READ MORE</span>
  </div>

  <div class="abs news-img" style="left:627px;top:1486px;background:linear-gradient(135deg,#4a4f55,#a7abb0 55%,#e4e5e6)" role="img" aria-label="Photo of hands working on a laptop beside paper documents"></div>
  <div class="abs news" style="left:870px;top:1480px">
    <h4>At vero eos et accu samu</h4>
    <div class="meta"><b></b>17/08/2017 &nbsp;|&nbsp; <b></b>Mara Lind</div>
    <p>Temporibus autem quibusdam et aut offi cis debitis aut rerum necessitatibus sae pe eveniet ut et voluptates.</p>
    <span class="more">READ MORE</span>
  </div>
</section>

<section class="brands">
  <h2 class="abs heading section-title" style="top:1842px">Our Brands</h2>
  <div class="abs brand-box" style="left:99px">Velora</div>
  <div class="abs brand-box" style="left:302px">Quintex</div>
  <div class="abs brand-box" style="left:505px">Norvo</div>
  <div class="abs brand-box" style="left:710px;font-size:24px">Aldren</div>
  <div class="abs brand-box" style="left:913px;font-size:24px">Sablecore</div>
</section>

<section class="contact">
  <svg class="abs contact-bg" width="1200" height="376" viewBox="0 0 1200 376" aria-hidden="true">
    <defs>
      <linearGradient id="contactGrad" x1="0" y1="0.5" x2="1" y2="0">
        <stop offset="0" stop-color="#0a2456"/>
        <stop offset="0.6" stop-color="#0e3d5e"/>
        <stop offset="1" stop-color="#1b7a3c"/>
      </linearGradient>
    </defs>
    <polygon points="0,0 1200,0 1200,376 0,237" fill="url(#contactGrad)"/>
  </svg>
  <h2 class="abs heading section-title contact-title" style="top:2182px">How to Contact Us</h2>
  <p class="abs contact-lead" style="top:2250px">Nam libero tempore, cum soluta nobis est eligendi optio cumque nihil impedit quo minus id quod maxime placeat facere possimus, omnis voluptas assumenda est, omnis dolor repellend uibusda</p>
  <div class="abs btn-outline contact-btn">CONTACT US</div>
</section>

<footer>
  <div class="abs foot-brand"><div class="mark"></div>Brelvanto</div>

  <div class="abs foot-col" style="left:414px;top:2564px">
    <h5>Information</h5>
    <ul><li>Help</li><li>FAQ</li><li>Support</li><li>Sitemap</li><li>Terms Of Use</li><li>Privacy Statement</li></ul>
  </div>

  <div class="abs foot-col" style="left:610px;top:2564px">
    <h5>Newsletter Subscription</h5>
    <p>Register your Email Address to get<br>Information about us</p>
    <div class="email-field">Email Address</div>
    <div class="subscribe">SUBSCRIBE</div>
  </div>

  <div class="abs foot-col" style="left:946px;top:2564px">
    <h5>Contact Us</h5>
    <div class="contact-row">
      <svg width="12" height="15" viewBox="0 0 12 15"><path d="M6 0a6 6 0 0 1 6 6c0 4-6 9-6 9S0 10 0 6a6 6 0 0 1 6-6z" fill="#f0901e"/><circle cx="6" cy="6" r="2.2" fill="#fff"/></svg>
      Corvelstrasse 14B<br>8050 Zürich
    </div>
    <div class="contact-row">
      <svg width="13" height="13" viewBox="0 0 13 13"><path d="M3 0l2.5 3-1.5 2a8 8 0 0 0 4 4l2-1.5 3 2.5-1.5 2.5C6 12.5 .5 7 .5 1.5z" fill="#f0901e"/></svg>
      1 555 010 0199
    </div>
    <div class="contact-row">
      <svg width="14" height="11" viewBox="0 0 14 11"><rect width="14" height="11" rx="1" fill="#f0901e"/><path d="M1 1.5l6 4.5 6-4.5" fill="none" stroke="#fff" stroke-width="1.3"/></svg>
      info@brelvanto-example.com
    </div>
  </div>

  <div class="abs rule"></div>
  <div class="abs copy">Copyrights © 2018, Brelvanto. All rights reserved.</div>
  <div class="abs social" style="left:976px" aria-label="Social link"></div>
  <div class="abs social" style="left:1008px" aria-label="Social link"></div>
  <div class="abs social" style="left:1040px" aria-label="Social link"></div>
  <div class="abs social" style="left:1073px" aria-label="Social link"></div>
</footer>

</body>
</html>
```